Business Cards for a law firm

Business cards for our law firm. Use our silhoette logo and OAK PARTNERS - check our website (www.oakpartners.example)

Contact Information for Business Card

our silhouette logo, OAK PARTNERS, 800-555-0147, Dorian Pemberton, dorian@oakpartners.example

Requirements
Must have
• our silhouette logo, OAK PARTNERS, 800-555-0147, Dorian Pemberton, dorian@oakpartners.example

```html
<!DOCTYPE html>
<html lang="en">
<head>
<meta charset="UTF-8">
<title>Oak Partners — Business Card</title>
<link rel="stylesheet" href="https://fonts.googleapis.com/css2?family=Montserrat:wght@400;500;700&display=swap">
<style>
  :root {
    --navy: #1f2f6e;
    --navy-soft: #2c3e84;
    --ink: #1c1c24;
    --paper: #ffffff;
    --paper-shade: #ececec;
    --backdrop: #e4e5ea;
  }
  * { box-sizing: border-box; margin: 0; padding: 0; }
  html, body { width: 1200px; height: 900px; overflow: hidden; }
  body {
    background: var(--backdrop);
    font-family: "Montserrat", Arial, sans-serif;
    position: relative;
  }
  .card {
    position: absolute;
    left: 250px;
    width: 700px;
    height: 400px;
    border-radius: 24px;
    overflow: hidden;
    box-shadow: 0 10px 30px rgba(20, 30, 70, 0.18);
  }
  .card-front {
    top: 40px;
    background: linear-gradient(180deg, var(--paper) 0%, var(--paper-shade) 100%);
  }
  .card-back {
    top: 460px;
    background: var(--navy);
    display: flex;
    align-items: center;
    justify-content: center;
  }
  .front-swoosh { position: absolute; inset: 0; width: 700px; height: 400px; }
  .brand {
    position: absolute;
    left: 66px;
    top: 166px;
    display: flex;
    align-items: center;
    gap: 12px;
  }
  .brand-dot {
    width: 24px; height: 24px;
    border-radius: 50%;
    background: var(--navy);
  }
  .brand-name {
    font-weight: 700;
    font-size: 26px;
    letter-spacing: 1px;
    color: var(--navy);
  }
  .divider {
    position: absolute;
    left: 380px;
    top: 60px;
    width: 3px;
    height: 200px;
    background: var(--navy);
  }
  .contact {
    position: absolute;
    left: 408px;
    top: 54px;
    color: var(--ink);
  }
  .contact-name {
    font-weight: 700;
    font-size: 22px;
    letter-spacing: 0.3px;
    color: var(--navy);
    line-height: 1.15;
    white-space: nowrap;
  }
  .contact-title {
    font-size: 13px;
    letter-spacing: 1px;
    margin-top: 2px;
  }
  .contact-address {
    font-size: 14px;
    line-height: 1.35;
    margin-top: 18px;
  }
  .contact-list {
    list-style: none;
    margin-top: 16px;
    font-size: 14px;
  }
  .contact-list li {
    display: flex;
    align-items: center;
    gap: 12px;
    line-height: 1.6;
    white-space: nowrap;
  }
  .contact-list svg { width: 14px; height: 14px; flex: none; fill: var(--navy); }
  .back-name {
    font-weight: 700;
    font-size: 60px;
    letter-spacing: 3px;
    color: var(--navy-soft);
  }
</style>
</head>
<body>

<section class="card card-front">
  <svg class="front-swoosh" viewBox="0 0 700 400" aria-hidden="true">
    <path d="M0,350 Q380,342 700,282 L700,400 L0,400 Z" fill="var(--navy)"/>
    <path d="M300,338 Q520,310 700,272" fill="none" stroke="var(--navy)" stroke-width="3"/>
    <path d="M350,332 Q550,302 700,265" fill="none" stroke="var(--navy)" stroke-width="2.5"/>
    <path d="M420,324 Q580,295 700,258" fill="none" stroke="var(--navy)" stroke-width="2"/>
  </svg>

  <div class="brand">
    <span class="brand-dot"></span>
    <span class="brand-name">OAK PARTNERS</span>
  </div>

  <div class="divider"></div>

  <div class="contact">
    <h1 class="contact-name">DORIAN PEMBERTON</h1>
    <p class="contact-title">OWNER</p>
    <p class="contact-address">1420 Harbor Ave #310,<br>Lakeview, CA 90000</p>
    <ul class="contact-list">
      <li>
        <svg viewBox="0 0 24 24"><path d="M6.6 10.8a15 15 0 0 0 6.6 6.6l2.2-2.2a1 1 0 0 1 1-.25 11.4 11.4 0 0 0 3.6.6 1 1 0 0 1 1 1V20a1 1 0 0 1-1 1A17 17 0 0 1 3 4a1 1 0 0 1 1-1h3.5a1 1 0 0 1 1 1c0 1.25.2 2.45.6 3.6a1 1 0 0 1-.25 1z"/></svg>
        <span>800-555-0147</span>
      </li>
      <li>
        <svg viewBox="0 0 24 24"><path d="M2 5h20v14H2z M4 7v.5l8 5 8-5V7l-8 5z" fill-rule="evenodd"/></svg>
        <span>dorian@oakpartners.example</span>
      </li>
      <li>
        <svg viewBox="0 0 24 24"><path d="M12 2a10 10 0 1 0 0 20 10 10 0 0 0 0-20zm-1 17.9A8 8 0 0 1 4.1 11H7c.1 3 1.5 6.2 4 8.9zM7 9H4.1A8 8 0 0 1 11 4.1C8.5 6.8 7.1 6 7 9zm6 10.9c2.5-2.7 3.9-5.9 4-8.9h2.9a8 8 0 0 1-6.9 8.9zM17 9c-.1-3-1.5-2.2-4-4.9A8 8 0 0 1 19.9 9z"/></svg>
        <span>www.oakpartners.example</span>
      </li>
    </ul>
  </div>
</section>

<section class="card card-back">
  <span class="back-name">OAK PARTNERS</span>
</section>

</body>
</html>
```